Building company buisness cards

We are looking for a sharp modern new look for our business cards.
We are a New Zealand based company that specialises in house and land packages.
We have attached a photo of the current logo and would like to see if it can be improved somehow if needed.
We are open to any colours but we have chosen green at this stage.
Feel free to change the font and make the logo smarter looking.
Play with the colours and see what looks best.

We want a card that looks so good know one will want to throw it away!

Target Market(s)

Home buyers

Industry/Entity Type

Building

Contact Information for Business Card

Derek Tolvane
0217394062
dtolvane@quillmarkhomesteads.co.nz
quillmarkhomesteads.co.nz

Font styles to use
Serif
Sans Serif

Colors

Designer to choose colors to be used in the design.

Requirements
Must have
• Logo and company name on one side, details on the other side
Nice to have
• Color codes for the original green are HEX #4a8028, RGB(74,128,40), CMYK(42,0,69,50)
• Round corners, Raised and/or spot UV

```html
<!DOCTYPE html>
<html lang="en">
<head>
<meta charset="utf-8">
<title>Quillmark Homesteads – Business Card</title>
<link rel="stylesheet" href="https://fonts.googleapis.com/css2?family=Cinzel:wght@600&family=Roboto:wght@400;500&display=swap">
<style>
  :root {
    --stage: #202020;
    --paper: #ffffff;
    --brand-green: #4a8028;
    --name-green: #5f9a3a;
    --ink-grey: #8a8a8a;
    --band-grey: #4d4d4d;
    --on-green: #f4f8f0;
  }
  html, body {
    margin: 0;
    padding: 0;
    width: 1125px;
    height: 1200px;
    overflow: hidden;
    background: var(--stage);
  }
  .canvas {
    position: relative;
    width: 1125px;
    height: 1200px;
  }
  .card {
    position: absolute;
    left: 150px;
    width: 825px;
    height: 472px;
    overflow: hidden;
  }
  .card--front {
    top: 98px;
    background: var(--paper);
  }
  .card--back {
    top: 630px;
    background: var(--brand-green);
  }

  /* Front: brand name block */
  .brand {
    position: absolute;
    left: 440px;
    top: 140px;
    width: 340px;
    text-align: center;
    font-family: "Cinzel", "Times New Roman", serif;
    font-weight: 600;
    color: var(--brand-green);
    line-height: 1;
  }
  .brand__line {
    display: block;
    font-size: 40px;
    letter-spacing: 1px;
  }
  .brand__line + .brand__line {
    margin-top: 8px;
  }

  /* Front: contact block */
  .contact {
    position: absolute;
    left: 41px;
    top: 302px;
    font-family: "Roboto", Arial, sans-serif;
  }
  .contact__name {
    margin: 0 0 18px;
    font-size: 28px;
    font-weight: 500;
    color: var(--name-green);
    letter-spacing: 0.3px;
  }
  .contact__list {
    list-style: none;
    margin: 0;
    padding: 0;
  }
  .contact__item {
    display: flex;
    align-items: center;
    height: 26px;
    font-size: 19px;
    color: var(--ink-grey);
  }
  .contact__icon {
    width: 18px;
    height: 18px;
    margin-right: 12px;
    flex: none;
  }
  .band {
    position: absolute;
    left: 0;
    bottom: 0;
    width: 825px;
    height: 21px;
  }

  /* Back */
  .back-brand {
    position: absolute;
    left: 0;
    top: 176px;
    width: 825px;
    text-align: center;
    font-family: "Cinzel", "Times New Roman", serif;
    font-weight: 600;
    font-size: 46px;
    line-height: 1.15;
    color: var(--on-green);
    letter-spacing: 2px;
  }
  .back-url {
    position: absolute;
    left: 0;
    top: 406px;
    width: 825px;
    text-align: center;
    font-family: "Roboto", Arial, sans-serif;
    font-size: 18px;
    letter-spacing: 4px;
    color: var(--on-green);
  }
</style>
</head>
<body>
<main class="canvas">

  <section class="card card--front" aria-label="Card front">
    <div class="brand">
      <span class="brand__line">Quillmark</span>
      <span class="brand__line">Homesteads</span>
    </div>

    <div class="contact">
      <h1 class="contact__name">DEREK TOLVANE</h1>
      <ul class="contact__list">
        <li class="contact__item">
          <svg class="contact__icon" viewBox="0 0 24 24" aria-hidden="true">
            <path fill="#4a8028" d="M6.6 10.8a15.1 15.1 0 0 0 6.6 6.6l2.2-2.2a1 1 0 0 1 1-.25 11.4 11.4 0 0 0 3.6.57 1 1 0 0 1 1 1V20a1 1 0 0 1-1 1A17 17 0 0 1 3 4a1 1 0 0 1 1-1h3.5a1 1 0 0 1 1 1c0 1.25.2 2.45.57 3.57a1 1 0 0 1-.25 1z"/>
          </svg>
          0217394062
        </li>
        <li class="contact__item">
          <svg class="contact__icon" viewBox="0 0 24 24" aria-hidden="true">
            <rect x="3" y="6" width="18" height="12" rx="1" fill="#4a8028"/>
            <path d="M3.5 6.5 12 13l8.5-6.5" fill="none" stroke="#ffffff" stroke-width="1.6"/>
          </svg>
          dtolvane@quillmarkhomesteads.co.nz
        </li>
        <li class="contact__item">
          <svg class="contact__icon" viewBox="0 0 24 24" aria-hidden="true">
            <circle cx="12" cy="12" r="9" fill="#4a8028"/>
            <path d="M7 8c2 0 3 1 3 3s-2 2-2 4M15 5c0 2 1 3 3 3M14 19c0-2 1-3 3-3" fill="none" stroke="#ffffff" stroke-width="1.5"/>
          </svg>
          quillmarkhomesteads.co.nz
        </li>
      </ul>
    </div>

    <svg class="band" viewBox="0 0 825 21" aria-hidden="true">
      <polygon points="0,0 542,0 536,21 0,21" fill="#4a8028"/>
      <polygon points="548,0 825,0 825,21 542,21" fill="#4d4d4d"/>
    </svg>
  </section>

  <section class="card card--back" aria-label="Card back">
    <div class="back-brand">QUILLMARK<br>HOMESTEADS</div>
    <div class="back-url">www.quillmarkhomesteads.co.nz</div>
  </section>

</main>
</body>
</html>
```